Copperleaf Roofing Business Card

This is my current business card. But I’d like to make some changes. Somewhere on the card I’d like to list some of the services we offer. Maybe on the back? But I’d still like to keep the red. White and black modern look.

-residential & commercial roofing
-Roof Repairs & Maintenance
-Storm Damage & Insurance Claims specialist
-Christmas Lights and permanent Christmas lights
Fencing. Windows. Gutters. Siding. Sheetrock, painting.

```html
<!DOCTYPE html>
<html lang="en">
<head>
<meta charset="utf-8">
<title>Copperleaf Roofing Co. — Business Card</title>
<link href="https://fonts.googleapis.com/css2?family=Audiowide&family=Questrial&display=swap" rel="stylesheet">
<style>
  :root {
    --red: #d41f26;
    --red-deep: #8e1116;
    --red-dark: #5e0a0d;
    --black: #141414;
    --ink: #3a3a3a;
    --grey: #8a8a8a;
    --white: #ffffff;
    --backdrop: #ecebe8;
  }
  * { box-sizing: border-box; margin: 0; padding: 0; }
  html, body { width: 1200px; height: 900px; overflow: hidden; }
  body {
    background: var(--backdrop);
    font-family: "Questrial", "Century Gothic", sans-serif;
    position: relative;
  }
  .card {
    position: absolute;
    left: 250px;
    width: 700px;
    height: 400px;
    border-radius: 28px;
    overflow: hidden;
    box-shadow: 0 10px 28px rgba(0,0,0,0.18);
  }
  .card--front { top: 35px; }
  .card--back { top: 465px; background: var(--white); }

  /* Front */
  .tartan-field {
    position: absolute; inset: 0;
    background: linear-gradient(135deg, var(--red-dark) 0%, var(--red) 40%, var(--red-deep) 70%, var(--red-dark) 100%);
  }
  .front-brand {
    position: absolute; inset: 0;
    display: flex; flex-direction: column; align-items: center; justify-content: center;
    gap: 18px;
  }
  .brand-dot {
    width: 120px; height: 120px; border-radius: 50%;
    background: var(--black);
    border: 4px solid var(--white);
  }
  .front-name {
    font-family: "Audiowide", sans-serif;
    color: var(--white);
    font-size: 40px;
    line-height: 1.05;
    text-align: center;
    letter-spacing: 1px;
  }

  /* Back */
  .back-brand {
    position: absolute; left: 40px; top: 105px; width: 250px;
    display: flex; flex-direction: column; align-items: center; gap: 14px;
  }
  .back-brand .brand-dot { width: 96px; height: 96px; background: var(--red); border: none; }
  .back-name {
    font-family: "Audiowide", sans-serif;
    color: var(--red);
    font-size: 27px;
    line-height: 1.05;
    text-align: center;
  }
  .divider {
    position: absolute; left: 305px; top: 40px; width: 1px; height: 165px;
    background: var(--grey);
  }
  .person { position: absolute; left: 330px; top: 40px; }
  .person-name {
    font-family: "Audiowide", sans-serif;
    font-size: 26px; color: var(--black);
  }
  .person-name .first { color: var(--red); }
  .person-role { font-size: 13px; color: var(--grey); letter-spacing: 1px; margin-top: 2px; }
  .contacts { list-style: none; margin-top: 26px; }
  .contacts li {
    display: flex; align-items: center; gap: 10px;
    font-size: 15px; color: var(--ink); margin-bottom: 7px;
  }
  .contacts svg { width: 15px; height: 15px; flex: none; }
  .services { position: absolute; left: 40px; top: 245px; right: 40px; }
  .services-title {
    font-size: 15px; font-weight: 700; color: var(--black);
    letter-spacing: 1px; margin-left: 240px; margin-bottom: 6px;
  }
  .services-list { list-style: none; font-size: 14.5px; color: var(--ink); line-height: 1.45; }
  .services-list .bullet { color: var(--red); margin: 0 6px 0 0; }
  .corner-band {
    position: absolute; right: -40px; bottom: -30px; width: 420px; height: 60px;
    transform: rotate(-14deg);
    background: linear-gradient(90deg, var(--red-deep), var(--red), var(--red-dark));
  }
</style>
</head>
<body>
  <section class="card card--front">
    <div class="tartan-field" role="img" aria-label="Red, black and white tartan plaid pattern"></div>
    <div class="front-brand">
      <div class="brand-dot"></div>
      <div class="front-name">COPPERLEAF<br>ROOFING CO.</div>
    </div>
  </section>

  <section class="card card--back">
    <div class="back-brand">
      <div class="brand-dot"></div>
      <div class="back-name">COPPERLEAF<br>ROOFING CO.</div>
    </div>
    <div class="divider"></div>
    <div class="person">
      <div class="person-name"><span class="first">DALE</span> MERCER</div>
      <div class="person-role">OWNER</div>
      <ul class="contacts">
        <li>
          <svg viewBox="0 0 24 24"><path fill="#d41f26" d="M6.6 10.8a15.1 15.1 0 0 0 6.6 6.6l2.2-2.2c.3-.3.7-.4 1-.2 1.1.4 2.3.6 3.6.6.6 0 1 .4 1 1V20c0 .6-.4 1-1 1C10.6 21 3 13.4 3 4c0-.6.4-1 1-1h3.5c.6 0 1 .4 1 1 0 1.3.2 2.5.6 3.6.1.3 0 .7-.2 1z"/></svg>
          682-555-0148
        </li>
        <li>
          <svg viewBox="0 0 24 24"><rect x="2" y="5" width="20" height="14" rx="1" fill="#d41f26"/><path d="M3 6l9 7 9-7" stroke="#fff" stroke-width="1.8" fill="none"/></svg>
          dale@copperleafroofing.co
        </li>
        <li>
          <svg viewBox="0 0 24 24" fill="none" stroke="#d41f26" stroke-width="1.8"><circle cx="12" cy="12" r="9"/><ellipse cx="12" cy="12" rx="4" ry="9"/><path d="M3 12h18M5 7h14M5 17h14"/></svg>
          www.copperleafroofing.co
        </li>
      </ul>
    </div>
    <div class="services">
      <div class="services-title">SERVICES</div>
      <ul class="services-list">
        <li><span class="bullet">◆</span>Residential &amp; Commercial Roofing <span class="bullet">◆</span>Roof Repairs &amp; Maintenance</li>
        <li><span class="bullet">◆</span>Storm Damage &amp; Insurance Claims Specialist</li>
        <li><span class="bullet">◆</span>Christmas Lights And Permanent Christmas Lights</li>
        <li><span class="bullet">◆</span>Fencing. Windows. Gutters. Siding. Sheetrock, painting</li>
      </ul>
    </div>
    <div class="corner-band" role="img" aria-label="Strip of red tartan plaid pattern"></div>
  </section>
</body>
</html>
```